Label for chemical drums for automotive products

I need a background label designing for a range of automotive cleaning products that go into proffesional users, dealerships and other companies. Not retail. They will have a logo at the top with a chemical name and description and safety data and usage in the middle and and address at the bottom.
The label size is approx A5
The label will be on silver tubs and clear drums
I've put a pic of a current label belong, just to show general layout. I HATE THOSE LABELS! The info on them will be the same IE name product details etc, it's a background that I'm looking for that looks highly proffesional and colourful and stands out.,but obviously the information that has to be on the product must be readable over the background your designing.
The veltrane auto logo is my logo that will be going on the label. I had it done on here
Car dealers, haulage companies, proffesional valeters
Automotive

```html
<!DOCTYPE html>
<html lang="en">
<head>
<meta charset="utf-8">
<title>VX - 40 Multi Purpose Cleaner Label</title>
<link rel="stylesheet" href="https://fonts.googleapis.com/css2?family=Jost:wght@400;600&family=Montserrat:wght@900&family=Oswald:wght@600&display=swap">
<style>
  :root {
    --leaf: #e2efc8;
    --sun: #fde08c;
    --sun-soft: #fce9ae;
    --white: #ffffff;
    --ink: #1a1a1a;
    --steel: #8c9196;
    --hazard: #d42a22;
    --edge: #9a9a9a;
  }
  html, body {
    margin: 0;
    padding: 0;
    overflow: hidden;
    background: #ffffff;
  }
  .label {
    position: relative;
    width: 857px;
    height: 1200px;
    overflow: hidden;
    background: var(--leaf);
    box-sizing: border-box;
    border-right: 1px solid var(--edge);
    border-bottom: 1px solid var(--edge);
    font-family: "Jost", sans-serif;
    color: var(--ink);
  }
  .backdrop {
    position: absolute;
    inset: 0;
  }
  .product-name {
    position: absolute;
    left: 270px;
    top: 390px;
    margin: 0;
    transform: translate(-50%, -50%) rotate(-55deg);
    font-family: "Montserrat", sans-serif;
    font-weight: 900;
    font-size: 112px;
    line-height: 1;
    white-space: nowrap;
    color: var(--ink);
    text-shadow:
      4px 0 0 var(--white), -4px 0 0 var(--white),
      0 4px 0 var(--white), 0 -4px 0 var(--white),
      3px 3px 0 var(--white), -3px -3px 0 var(--white),
      3px -3px 0 var(--white), -3px 3px 0 var(--white);
  }
  .brand {
    position: absolute;
    left: 62px;
    top: 690px;
    margin: 0;
    font-family: "Jost", sans-serif;
    font-weight: 600;
    font-size: 62px;
    line-height: 1;
    white-space: nowrap;
    color: var(--steel);
  }
  .line {
    display: block;
    white-space: nowrap;
  }
  .line.fill {
    text-align: justify;
    text-align-last: justify;
  }
  .info {
    position: absolute;
    left: 427px;
    top: 824px;
    width: 252px;
    font-size: 16.5px;
    line-height: 20.3px;
  }
  .info h2 {
    margin: 0 0 2px;
    font-size: 16.5px;
    font-weight: 600;
    line-height: 20px;
  }
  .info p {
    margin: 0 0 18px;
  }
  .safety {
    position: absolute;
    left: 63px;
    top: 1042px;
    width: 616px;
    font-size: 14px;
    line-height: 18.2px;
  }
  .safety h2 {
    margin: 0;
    font-size: 14px;
    font-weight: 600;
    line-height: 18.2px;
  }
  .safety p {
    margin: 0;
  }
  .hazard {
    position: absolute;
    left: 698px;
    width: 112px;
    height: 112px;
  }
  .hazard-top { top: 860px; }
  .hazard-bottom { top: 979px; }
  .volume {
    position: absolute;
    left: 697px;
    top: 1113px;
    margin: 0;
    font-family: "Oswald", sans-serif;
    font-weight: 600;
    font-size: 36px;
    line-height: 1;
  }
</style>
</head>
<body>
<div class="label">
  <svg class="backdrop" width="857" height="1200" viewBox="0 0 857 1200" aria-hidden="true">
    <defs>
      <radialGradient id="bubble" cx="50%" cy="50%" r="50%">
        <stop offset="0%" stop-color="#ffffff" stop-opacity="0.55"/>
        <stop offset="100%" stop-color="#ffffff" stop-opacity="0.2"/>
      </radialGradient>
    </defs>
    <path d="M330 0 H857 V240 C760 300 700 330 640 360 C700 220 560 70 330 0 Z" fill="var(--sun)"/>
    <path d="M590 0 H857 V50 C780 30 700 15 590 0 Z" fill="var(--sun-soft)"/>
    <path d="M0 40 C260 40 520 140 610 340 C650 430 640 560 600 660 C660 520 640 360 560 250 C450 110 250 60 0 60 Z" fill="var(--white)"/>
    <path d="M857 210 C760 260 720 300 690 350 C760 300 810 280 857 270 Z" fill="var(--white)"/>
    <path d="M857 0 C800 80 720 180 620 230 L640 250 C740 200 820 110 857 40 Z" fill="var(--white)" opacity="0.85"/>
    <path d="M110 1200 L230 995 L380 1200 Z" fill="var(--sun)"/>
    <path d="M0 1080 C200 1010 420 990 700 1010 L700 1030 C420 1010 200 1030 0 1100 Z" fill="var(--white)" opacity="0.9"/>
    <path d="M230 995 C300 930 380 880 470 850 L470 866 C390 895 310 940 245 1005 Z" fill="var(--white)"/>
    <circle cx="666" cy="592" r="68" fill="url(#bubble)"/>
    <circle cx="705" cy="593" r="58" fill="url(#bubble)"/>
    <circle cx="626" cy="766" r="26" fill="url(#bubble)"/>
  </svg>

  <h1 class="product-name">VX - 40</h1>

  <p class="brand">Veltrane Auto</p>

  <div class="info">
    <h2>Description :</h2>
    <p>
      <span class="line fill">Total performance multi purpose</span>
      <span class="line fill">cleaner with Increased stegth for</span>
      <span class="line fill">use on upholstery, paint work,</span>
      <span class="line">glass, hard sufrces etc.</span>
    </p>
    <h2>Method of use :</h2>
    <p>
      <span class="line fill">Apply using a spray, sponge or</span>
      <span class="line fill">cloth. Dilute 1:5 - 1:50</span>
      <span class="line">dependant on application.</span>
    </p>
  </div>

  <svg class="hazard hazard-top" viewBox="0 0 112 112" role="img" aria-label="Irritant hazard pictogram">
    <polygon points="56,3 109,56 56,109 3,56" fill="#ffffff" stroke="var(--hazard)" stroke-width="4"/>
    <path d="M51 26 H61 L58 70 H54 Z" fill="var(--ink)"/>
    <circle cx="56" cy="80" r="6" fill="var(--ink)"/>
  </svg>
  <svg class="hazard hazard-bottom" viewBox="0 0 112 112" role="img" aria-label="Empty hazard pictogram frame">
    <polygon points="56,3 109,56 56,109 3,56" fill="#ffffff" stroke="var(--hazard)" stroke-width="4"/>
  </svg>

  <div class="safety">
    <h2>Health &amp; Safety:</h2>
    <p>
      <span class="line fill">Causes serious eye irrtation. Wash hands thoroughly after handling. Wear protactive</span>
      <span class="line">gloves/protactive clothing/eye protaction/face protection.</span>
      <span class="line">If in Eyes:</span>
      <span class="line fill">Rinse cautiously with water for several minutes. Remove contact lenses. If present and easy</span>
      <span class="line">to do. Continue rinsing. If eye irritation persists - Get medical advice attention.</span>
      <span class="line">Keep out of reach of children.</span>
    </p>
  </div>

  <p class="volume">5 Litres</p>
</div>
</body>
</html>
```